Property Development Business Cards

I need a business card design for Tallbridge Holdings Pty Ltd. We are a property development company in Australia and our name defines the five values that we adhere to, being Profitable, Partnerships, Quality Developments, Eco Friendly and Enduring Design.

I have attached the current logo that I use, it is just five yellow circles connected to a single cricle in the middle.

Target Market(s)

Our Target audience is real estate agents, owners of properties, builders and other trades

Industry/Entity Type

Business

Requirements
Must have
• Want to have two sides to the card, one with details and one to just highlight the company

```html
<!DOCTYPE html>
<html lang="en">
<head>
<meta charset="utf-8">
<title>Tallbridge Holdings Pty Ltd – Business Card</title>
<link rel="stylesheet" href="https://fonts.googleapis.com/css2?family=Open+Sans:wght@400;600&display=swap">
<style>
  :root {
    --page-bg: #ffffff;
    --card-bg: #ffffff;
    --card-border: #c9c9c9;
    --brand-blue: #1f63ae;
    --text-grey: #5a5a5a;
    --accent-yellow: #f6c21c;
  }
  * { box-sizing: border-box; margin: 0; padding: 0; }
  html, body {
    width: 1200px;
    height: 330px;
    overflow: hidden;
    background: var(--page-bg);
    font-family: "Open Sans", Verdana, sans-serif;
  }
  .sheet {
    position: relative;
    width: 1200px;
    height: 330px;
  }
  .card {
    position: absolute;
    top: 9px;
    width: 590px;
    height: 312px;
    background: var(--card-bg);
    border: 1.5px solid var(--card-border);
  }
  .card--front { left: 9px; }
  .card--back  { left: 601px; }

  /* Front */
  .front-mark {
    position: absolute;
    left: 50%;
    top: 125px;
    width: 92px;
    height: 92px;
    margin: -46px 0 0 -46px;
    border-radius: 50%;
    background: var(--accent-yellow);
  }
  .front-name {
    position: absolute;
    left: 0;
    right: 0;
    top: 268px;
    text-align: center;
    font-size: 24px;
    font-weight: 400;
    color: var(--brand-blue);
    line-height: 1;
  }

  /* Back */
  .back-brand {
    position: absolute;
    top: 30px;
    right: 28px;
    display: flex;
    align-items: center;
    gap: 10px;
  }
  .back-brand__dot {
    width: 26px;
    height: 26px;
    border-radius: 50%;
    background: var(--accent-yellow);
  }
  .back-brand__name {
    font-size: 16px;
    font-weight: 600;
    color: var(--brand-blue);
  }
  .contact-name {
    position: absolute;
    left: 24px;
    top: 78px;
    font-size: 27px;
    font-weight: 600;
    color: var(--brand-blue);
    line-height: 1.2;
  }
  .contact-list {
    position: absolute;
    left: 24px;
    top: 154px;
    list-style: none;
    font-size: 16px;
    color: var(--text-grey);
    line-height: 24.5px;
  }
  .contact-web {
    position: absolute;
    left: 24px;
    top: 263px;
    font-size: 16px;
    color: var(--text-grey);
  }
</style>
</head>
<body>
  <main class="sheet">
    <section class="card card--front" aria-label="Card front">
      <div class="front-mark"></div>
      <p class="front-name">Tallbridge Holdings Pty Ltd</p>
    </section>

    <section class="card card--back" aria-label="Card back">
      <div class="back-brand">
        <span class="back-brand__dot"></span>
        <span class="back-brand__name">Tallbridge Holdings</span>
      </div>
      <h1 class="contact-name">Marcus Denholm</h1>
      <ul class="contact-list">
        <li>Mobile: 0412.555.318</li>
        <li>Email: Marcus@TallbridgeHoldings.com.au</li>
        <li>P.O. Box 127</li>
        <li>Ferndale, ACT 2915</li>
      </ul>
      <p class="contact-web">www.TallbridgeHoldings.com.au</p>
    </section>
  </main>
</body>
</html>
```